Financial Advisor Resource Firm needs business card design

Need business card design for company in Omaha NE called Meridale Circle. We provide resources to financial advisors....workshop programs, retirement analysis, and insurance planning. I would like to see designs that use grays, greens, black, and white colors. The final design should communicate 'collaboration' and be simple yet attractive to financial planning clients. I will attached our logo and another picture of a puzzle piece coming together. I would like the incorporate the puzzle picture somehow, maybe on the back somehow, with color or just the gray scale....OR, the picture be the front of the card with 'Meridale' definition on it (see upload) and then company logo, employee name, title, address on the back (see ppt uploaded). The following disclosure needs to be included somewhere- Advisory services offered through Stonebrook Assets, LLC.
Updates

I uploaded a svg and ai file of the logo

Target Market(s)

Financial planning clients and financial advisors....so pretty diverse age range of about 40-70.

Industry/Entity Type

Financial Planning

Contact Information for Business Card

Tobias L. Fenwright, MBA
Founder/President
5287 E. Larkin Road
Suite 230
Omaha, NE 68190
Phone- (402) 555-0147
Cell- (402) 555-0183
Fax- (402) 555-0129
email- tobias@meridaleplan.example
web address- www.meridaleplan.example

Colors
1b1b1b
474747
d3d3d3
ffffff
9bcb3c
abd036

Requirements
Must have
• Must include logo provided, must be 2 sided, and must have disclosure...all of these items listed in project description

```html
<!DOCTYPE html>
<html lang="en">
<head>
<meta charset="utf-8">
<title>Meridale Circle – Business Card</title>
<link href="https://fonts.googleapis.com/css2?family=Lato:wght@400;700&display=swap" rel="stylesheet">
<style>
  :root {
    --backdrop: #2a2a2a;
    --card-light: #eeeeee;
    --ink: #1b1b1b;
    --ink-soft: #474747;
    --rule: #474747;
    --green: #8cc63f;
    --green-deep: #7ab52f;
    --white: #ffffff;
  }
  * { margin: 0; padding: 0; box-sizing: border-box; }
  html, body { width: 1200px; height: 1200px; overflow: hidden; }
  body {
    background: var(--backdrop);
    font-family: "Lato", Arial, sans-serif;
    position: relative;
  }
  .card {
    position: absolute;
    top: 310px;
    width: 364px;
    height: 594px;
    box-shadow: 0 4px 10px rgba(0,0,0,0.45);
  }
  /* Front side */
  .card-front {
    left: 234px;
    background: var(--card-light);
    color: var(--ink);
    text-align: center;
  }
  .brand {
    position: absolute;
    top: 128px;
    left: 0; right: 0;
    display: flex;
    justify-content: center;
    align-items: center;
    gap: 10px;
  }
  .brand-dot {
    width: 16px; height: 16px;
    border-radius: 50%;
    background: var(--green);
  }
  .brand-name {
    font-size: 29px;
    font-weight: 700;
    letter-spacing: 2px;
    color: var(--ink);
  }
  .person {
    position: absolute;
    top: 263px;
    left: 0; right: 0;
  }
  .person-name {
    font-size: 19px;
    font-weight: 700;
    color: var(--green);
    line-height: 22px;
  }
  .person-name .credential { font-weight: 400; font-size: 17px; }
  .person-title { font-size: 16px; line-height: 20px; }
  .divider {
    position: absolute;
    left: 0; right: 0;
    display: flex;
    justify-content: center;
    align-items: center;
    gap: 6px;
  }
  .divider::before, .divider::after {
    content: "";
    width: 56px;
    height: 1px;
    background: var(--rule);
  }
  .divider svg { width: 24px; height: 24px; display: block; }
  .info {
    position: absolute;
    left: 0; right: 0;
    font-size: 16px;
    line-height: 20px;
  }
  /* Back side */
  .card-back {
    left: 627px;
    overflow: hidden;
    color: var(--white);
    text-align: center;
  }
  .back-photo {
    position: absolute;
    inset: 0;
    background:
      radial-gradient(ellipse at 55% 58%, #d8d8d8 0%, #9a9a9a 30%, transparent 60%),
      linear-gradient(180deg, #cfcfcf 0%, #8f8f8f 40%, #5a5a5a 70%, #2c2c2c 100%);
  }
  .tagline {
    position: absolute;
    top: 256px;
    left: 0; right: 0;
    font-size: 16px;
    line-height: 20px;
  }
  .back-rule {
    position: absolute;
    top: 496px;
    left: 24px; right: 0;
    height: 1px;
    background: rgba(255,255,255,0.4);
  }
  .disclosure {
    position: absolute;
    top: 511px;
    left: 0; right: 0;
    font-size: 17px;
    line-height: 20px;
    text-transform: uppercase;
  }
</style>
</head>
<body>

<section class="card card-front">
  <div class="brand">
    <span class="brand-dot"></span>
    <span class="brand-name">MERIDALE CIRCLE</span>
  </div>

  <div class="person">
    <p class="person-name">TOBIAS L. FENWRIGHT, <span class="credential">MBA</span></p>
    <p class="person-title">Founder/President</p>
  </div>

  <div class="divider" style="top:316px">
    <svg viewBox="0 0 24 24" aria-hidden="true">
      <circle cx="12" cy="12" r="10.5" fill="none" stroke="var(--green)" stroke-width="2"/>
      <path d="M8.6 7.2c.4-.4 1-.4 1.3 0l1 1.3c.3.4.2.9-.1 1.2l-.6.5c.5 1.1 1.4 2 2.5 2.6l.5-.6c.3-.3.8-.4 1.2-.1l1.3 1c.4.3.4.9 0 1.3l-.7.7c-.6.6-1.6.7-2.4.2-1.9-1.1-3.4-2.6-4.5-4.5-.5-.8-.4-1.8.2-2.4z" fill="var(--green)"/>
    </svg>
  </div>
  <div class="info" style="top:343px">
    <p>(402) 555-0147</p>
    <p>(402) 555-0183</p>
    <p>(402) 555-0129</p>
  </div>

  <div class="divider" style="top:409px">
    <svg viewBox="0 0 24 24" aria-hidden="true">
      <circle cx="12" cy="12" r="10.5" fill="none" stroke="var(--green)" stroke-width="2"/>
      <circle cx="12" cy="12" r="5.5" fill="var(--green)"/>
      <path d="M6.5 12h11M12 6.5c-2 2.8-2 8.2 0 11M12 6.5c2 2.8 2 8.2 0 11" stroke="var(--card-light)" stroke-width="1" fill="none"/>
    </svg>
  </div>
  <div class="info" style="top:434px">
    <p>tobias@meridaleplan.example</p>
    <p>www.meridaleplan.example</p>
  </div>

  <div class="divider" style="top:482px">
    <svg viewBox="0 0 24 24" aria-hidden="true">
      <circle cx="12" cy="12" r="10.5" fill="none" stroke="var(--green)" stroke-width="2"/>
      <path d="M12 5.5c-2.5 0-4.3 1.9-4.3 4.3 0 3.1 4.3 7.7 4.3 7.7s4.3-4.6 4.3-7.7c0-2.4-1.8-4.3-4.3-4.3z" fill="var(--green)"/>
      <circle cx="12" cy="9.8" r="1.6" fill="var(--card-light)"/>
    </svg>
  </div>
  <div class="info" style="top:512px">
    <p>5287 E. Larkin Road</p>
    <p>Suite 230 Omaha, NE 68190</p>
  </div>
</section>

<section class="card card-back">
  <div class="back-photo" role="img" aria-label="Grayscale photo of several hands fitting jigsaw puzzle pieces together"></div>
  <p class="tagline">To come together and unite<br>in common interest and focus</p>
  <div class="back-rule"></div>
  <p class="disclosure">Advisory services offered<br>through Stonebrook Assets, LLC.</p>
</section>

</body>
</html>
```